Termite Mailer September 2021

We need a clean modern looking flyer advertising termites via the mail.

Size should be 9"x6"

Our tagline is "The Smarter Approach to Pest Control"

Something along the stylistic design of these:

https://pics.lumora-share.net/Qk82vLmTzPwX4rNa1

https://pics.lumora-share.net/Hd37nBcYxTqW9sKe5

https://pics.lumora-share.net/Zr61pMfVaLuE2jGo8

https://www.cardvistaprint.net/wp-content/uploads/designs/img/Pest-Prevention-Postcard-PST-1003.jpg

Should include some of this verbiage:

HAVE YOU SCHEDULED YOUR ANNUAL TERMITE INSPECTION? - MAKE IT IN RED

DON'T WAIT. PROTECT YOUR HOME TODAY!

ABSOLUTELY FREE INSPECTION. NO OBLIGATION.

TERMITES CAN CAUSE SEVERE DAMAGE TO YOUR HOME.

BRIMVALE LOGO

THE SMARTER APPROACH TO PEST CONTROL.

PROTECT YOUR MOST VALUABLE ASSET.

10% DISCOUNT ON ANY SERVICE GUARANTEED IF YOU CALL TODAY.

INCLUDE A PICTURE OF A TERMITE AS WELL SOMEWHERE AND WOOD DAMAGE.

Target Market(s)

Homeowners in Southern California USA

Industry/Entity Type

Pest Control/Extermination

Font styles to use
Other font styles liked:
• Chaparral Pro Italic, Brava Slab

Requirements
Must have
• Clean design, picture of house, picture of Termite, 10% off coupon and call to action on the back
Should not have
• Bad looking houses, colors that don't match our logo

```html
<!DOCTYPE html>
<html lang="en">
<head>
<meta charset="utf-8">
<title>Brimvale Pest Control – Termite Mailer</title>
<link rel="stylesheet" href="https://fonts.googleapis.com/css2?family=Anton&family=Montserrat:wght@300;400;500;600;700;800;900&family=Oswald:wght@500;600;700&display=swap">
<style>
  :root {
    --navy: #1447a8;
    --blue-light: #1f56cf;
    --blue-dark: #0a2c86;
    --green: #6cc04a;
    --green-dark: #4fa32f;
    --red: #e3141b;
    --yellow: #ffe100;
    --ink: #1c1c1c;
    --black-band: #0f0f10;
    --white: #ffffff;
    --page: #e9e9e9;
    --rule: #9a9a9a;
  }
  * { box-sizing: border-box; margin: 0; padding: 0; }
  html, body { width: 1200px; height: 2259px; overflow: hidden; }
  body { background: var(--page); position: relative; font-family: "Montserrat", sans-serif; }

  .postcard {
    position: absolute; left: 80px; width: 1040px; height: 693px;
    background: var(--white); overflow: hidden;
    box-shadow: 0 14px 30px rgba(0,0,0,.22);
  }
  .postcard--front { top: 376px; }
  .postcard--back { top: 1189px; }
  .abs { position: absolute; line-height: 1; white-space: nowrap; }

  /* ---------- FRONT ---------- */
  .front-question { left: 48px; top: 26px; font-size: 17.5px; font-weight: 600; color: var(--ink); letter-spacing: .2px; }
  .front-headline { left: 41px; top: 54px; font-size: 31px; font-weight: 800; color: var(--navy); letter-spacing: .3px; }
  .front-headline .accent { color: var(--green); }

  .offer-panel { position: absolute; inset: 0; }
  .offer-panel__blue { position: absolute; inset: 0;
    background: radial-gradient(ellipse at 45% 45%, var(--blue-light) 0%, var(--blue-dark) 85%);
    clip-path: polygon(0 109px, 462px 109px, 377px 414px, 0 414px); }
  .offer-panel__green { position: absolute; inset: 0; background: var(--green);
    clip-path: polygon(0 414px, 377px 414px, 339px 550px, 0 550px); }

  .dont-wait { left: 0; width: 450px; text-align: center; top: 134px; font-family: "Anton", sans-serif;
    font-size: 66px; color: var(--red); letter-spacing: -.5px; }
  .today-bar { position: absolute; left: 60px; top: 212px; width: 316px; height: 33px; background: #000;
    transform: skewX(-12deg); display: flex; align-items: center; justify-content: center; }
  .today-bar span { font-family: "Oswald", sans-serif; font-weight: 700; font-size: 21px; color: var(--yellow);
    transform: skewX(-2deg); letter-spacing: .2px; }
  .absolutely { left: 35px; width: 321px; top: 266px; text-align: center; font-size: 13.5px; letter-spacing: 6px;
    color: var(--white); font-weight: 500; }
  .inspection-box { position: absolute; left: 35px; top: 273px; width: 321px; height: 96px;
    border: 1.5px solid rgba(255,255,255,.85); border-top: none; border-radius: 0 0 6px 6px; }
  .inspection-box::before, .inspection-box::after { content: ""; position: absolute; top: 0; height: 1.5px;
    background: rgba(255,255,255,.85); width: 52px; }
  .inspection-box::before { left: 0; }
  .inspection-box::after { right: 0; }
  .free-inspection { left: 35px; width: 321px; top: 293px; text-align: center; font-family: "Oswald", sans-serif;
    font-weight: 700; font-size: 46px; color: var(--white); letter-spacing: -.3px; }
  .no-obligation { position: absolute; left: 95px; top: 356px; width: 202px; height: 28px; border-radius: 14px;
    background: var(--yellow); color: #000; font-weight: 800; font-size: 15.5px;
    display: flex; align-items: center; justify-content: center; }

  .damage-word { color: var(--white); font-weight: 800; }
  .damage-small { color: var(--white); font-weight: 400; }
  .termites-title { left: 41px; top: 427px; font-size: 33px; }
  .termites-line2 { left: 82px; top: 465px; font-size: 16px; }
  .termites-damage { left: 152px; top: 484px; font-size: 33px; }
  .termites-line4 { left: 157px; top: 519px; font-size: 17px; }
  .termites-line4 b { font-weight: 800; }

  .photo { position: absolute; inset: 0; }
  .photo--termite { background: radial-gradient(ellipse at 60% 55%, #b9652a 0%, #6e4a30 30%, #2c2a33 80%);
    clip-path: polygon(504px 0, 716px 0, 667px 186px, 452px 186px); }
  .photo--swarm { background: radial-gradient(ellipse at 50% 50%, #b88a5d 0%, #7a4f2c 45%, #3a2416 90%);
    clip-path: polygon(450px 194px, 665px 194px, 620px 367px, 402px 367px); }
  .photo--wall { background: linear-gradient(150deg, #e5e7ea 0%, #c9cdd1 55%, #9d8e7c 100%);
    clip-path: polygon(400px 375px, 618px 375px, 572px 550px, 351px 550px); }
  .photo--house { background: linear-gradient(180deg, #3f8fe0 0%, #8cc0ee 30%, #6f8798 50%, #58728a 65%, #5b9a32 82%, #7cc23e 100%);
    clip-path: polygon(730px 0, 1040px 0, 1040px 550px, 586px 550px); }

  .front-footer { position: absolute; left: 0; top: 550px; width: 1040px; height: 143px; background: var(--white); }
  .brand { display: flex; align-items: center; gap: 9px; }
  .brand__dot { width: 26px; height: 26px; border-radius: 50%; background: var(--green); flex: none; }
  .brand__name { font-weight: 800; color: var(--navy); line-height: 1; letter-spacing: .5px; }
  .front-footer .brand { position: absolute; left: 38px; top: 54px; }
  .front-footer .brand__name { font-size: 31px; }
  .rule { position: absolute; width: 1.5px; background: var(--rule); }
  .front-footer .rule--a { left: 305px; top: 36px; height: 72px; }
  .front-footer .rule--b { left: 740px; top: 36px; height: 72px; }
  .tagline-top { left: 337px; top: 37px; font-size: 23px; font-weight: 400; color: var(--ink); }
  .tagline-main { left: 389px; top: 67px; font-size: 38px; font-weight: 800; color: var(--navy); }
  .tagline-main .to { color: var(--ink); }

  .phone-pill { position: absolute; display: flex; align-items: center; gap: 8px; padding: 0 14px 0 8px;
    border: 2px solid var(--navy); border-radius: 20px; background: var(--white);
    font-weight: 800; color: var(--navy); line-height: 1; }
  .phone-pill__icon { width: 22px; height: 22px; flex: none; }
  .front-footer .phone-pill { left: 775px; top: 40px; height: 38px; font-size: 26px; }
  .web { font-weight: 500; color: var(--ink); }
  .web .accent { color: var(--navy); font-weight: 600; }
  .front-footer .web { left: 778px; top: 90px; font-size: 19px; }

  /* ---------- BACK ---------- */
  .back-art { position: absolute; inset: 0; }
  .protect-title { left: 46px; top: 28px; font-size: 45px; font-weight: 800; color: var(--white); letter-spacing: .5px; }
  .protect-sub { left: 44px; top: 78px; font-size: 31px; font-weight: 300; color: var(--white); letter-spacing: .3px; }

  .discount-title { left: 46px; top: 443px; width: 320px; text-align: center; font-size: 41px; font-weight: 800; color: var(--white); }
  .bar { position: absolute; display: flex; align-items: center; justify-content: center; transform: skewX(-14deg); }
  .bar span { font-family: "Oswald", sans-serif; font-weight: 700; transform: skewX(4deg); letter-spacing: .2px; }
  .bar--yellow { left: 50px; top: 489px; width: 322px; height: 31px; background: var(--yellow); }
  .bar--yellow span { color: #000; font-size: 22px; }
  .bar--green { left: 88px; top: 524px; width: 246px; height: 26px; background: var(--green); }
  .bar--green span { color: var(--white); font-size: 18px; }

  .address { position: absolute; left: 35px; top: 602px; display: flex; gap: 7px; color: var(--white);
    font-size: 17px; font-weight: 400; line-height: 25px; }
  .address svg { width: 13px; height: 17px; margin-top: 4px; flex: none; }
  .postcard--back .rule { left: 243px; top: 600px; height: 74px; background: #8a8a8a; }
  .postcard--back .phone-pill { left: 265px; top: 600px; height: 34px; font-size: 24px; }
  .postcard--back .web { left: 265px; top: 650px; font-size: 18px; color: var(--white); }
  .postcard--back .web .accent { color: var(--white); }

  .pest-badge { position: absolute; width: 122px; height: 122px; border-radius: 50%;
    border: 4px solid var(--navy); background: radial-gradient(circle at 50% 50%, #c46a2a 0%, #f2f2f2 55%, #ffffff 70%);
    box-shadow: 0 0 0 3px var(--white); }
  .pest-badge--bedbug { left: 424px; top: 89px; }
  .pest-badge--wasp { left: 377px; top: 235px; background: radial-gradient(circle at 50% 50%, #e9c21e 0%, #3a3a3a 40%, #f2f2f2 62%, #ffffff 72%); }
  .pest-badge--ant { left: 390px; top: 379px; background: radial-gradient(circle at 50% 50%, #8a2b1b 0%, #e9e9e9 58%, #ffffff 72%); }

  .postcard--back .brand { position: absolute; left: 590px; top: 46px; }
  .postcard--back .brand__name { font-size: 31px; }
  .license { position: absolute; left: 658px; top: 110px; border: 1.5px solid var(--ink); border-radius: 3px;
    padding: 4px 9px; font-size: 13.5px; font-weight: 600; color: var(--ink); line-height: 1; }
  .stamp-box { position: absolute; left: 874px; top: 39px; width: 121px; height: 109px; border: 2px solid #333; }
  .address-line { position: absolute; left: 686px; width: 309px; height: 1.5px; background: #555; }
</style>
</head>
<body>

<!-- Front of the mailer -->
<section class="postcard postcard--front" aria-label="Mailer front">
  <p class="abs front-question">HAVE YOU SCHEDULED YOUR ANNUAL</p>
  <h1 class="abs front-headline">TERMITE <span class="accent">INSPECTION?</span></h1>

  <div class="offer-panel">
    <div class="offer-panel__blue"></div>
    <div class="offer-panel__green"></div>
  </div>

  <h2 class="abs dont-wait">DON'T WAIT.</h2>
  <div class="today-bar"><span>PROTECT YOUR HOME TODAY!</span></div>
  <div class="inspection-box"></div>
  <p class="abs absolutely">ABSOLUTELY</p>
  <p class="abs free-inspection">FREE INSPECTION</p>
  <div class="no-obligation">NO OBLIGATION</div>

  <p class="abs damage-word termites-title">TERMITES</p>
  <p class="abs damage-small termites-line2">CAN CAUSE SEVERE</p>
  <p class="abs damage-word termites-damage">DAMAGE</p>
  <p class="abs damage-small termites-line4">TO YOUR <b>HOME</b></p>

  <div class="photo photo--termite" role="img" aria-label="Close-up photo of a termite on wood"></div>
  <div class="photo photo--swarm" role="img" aria-label="Photo of a mass of termites"></div>
  <div class="photo photo--wall" role="img" aria-label="Photo of a hand pointing at termite mud tubes on a wall"></div>
  <div class="photo photo--house" role="img" aria-label="Photo of a blue-grey two-storey house with green lawn under a blue sky"></div>

  <footer class="front-footer">
    <div class="brand"><span class="brand__dot"></span><span class="brand__name">BRIMVALE</span></div>
    <span class="rule rule--a"></span>
    <p class="abs tagline-top">The Smarter Approach</p>
    <p class="abs tagline-main"><span class="to">to</span> Pest Control</p>
    <span class="rule rule--b"></span>
    <div class="phone-pill">
      <svg class="phone-pill__icon" viewBox="0 0 24 24"><circle cx="12" cy="12" r="12" fill="#6cc04a"/><path d="M8.6 6.2l1.6 2.6c.3.5.2 1-.2 1.4l-.9.8c.7 1.6 2 2.9 3.6 3.6l.8-.9c.4-.4.9-.5 1.4-.2l2.6 1.6c.5.3.6.9.3 1.4l-.8 1.1c-.5.7-1.4 1-2.2.8-3.9-1-6.9-4-7.9-7.9-.2-.8.1-1.7.8-2.2l1.1-.8c.5-.3 1.1-.2 1.4.3z" fill="#fff"/></svg>
      714-555-0148
    </div>
    <p class="abs web">www.go<span class="accent">brimvale</span>.com</p>
  </footer>
</section>

<!-- Back of the mailer -->
<section class="postcard postcard--back" aria-label="Mailer back">
  <svg class="back-art" width="1040" height="693" viewBox="0 0 1040 693">
    <rect x="0" y="0" width="700" height="129" fill="#6cc04a"/>
    <rect x="0" y="129" width="700" height="295" fill="#9c8a74" role="img" aria-label="Photo of termite-damaged wood"/>
    <defs>
      <linearGradient id="woodTone" x1="0" y1="0" x2="1" y2="1">
        <stop offset="0" stop-color="#d9dcdf"/>
        <stop offset=".45" stop-color="#8a6f55"/>
        <stop offset=".8" stop-color="#5a4634"/>
        <stop offset="1" stop-color="#b8aa97"/>
      </linearGradient>
      <radialGradient id="blueBand" cx=".4" cy=".5" r=".8">
        <stop offset="0" stop-color="#1f56cf"/>
        <stop offset="1" stop-color="#0a2c86"/>
      </radialGradient>
    </defs>
    <rect x="0" y="129" width="700" height="295" fill="url(#woodTone)"/>
    <rect x="0" y="424" width="700" height="151" fill="url(#blueBand)"/>
    <rect x="0" y="575" width="760" height="118" fill="#0f0f10"/>
    <ellipse cx="732" cy="340" rx="364" ry="414" fill="none" stroke="#6cc04a" stroke-width="2.5"/>
    <ellipse cx="732" cy="340" rx="350" ry="400" fill="#ffffff"/>
    <rect x="700" y="0" width="340" height="693" fill="#ffffff"/>
  </svg>

  <h2 class="abs protect-title">PROTECT YOUR</h2>
  <p class="abs protect-sub">MOST VALUABLE ASSET</p>

  <div class="pest-badge pest-badge--bedbug" role="img" aria-label="Bed bug inside a no-entry circle"></div>
  <div class="pest-badge pest-badge--wasp" role="img" aria-label="Wasp inside a no-entry circle"></div>
  <div class="pest-badge pest-badge--ant" role="img" aria-label="Ant inside a no-entry circle"></div>

  <h3 class="abs discount-title">10% DISCOUNT</h3>
  <div class="bar bar--yellow"><span>ON ANY SERVICE GUARANTEED</span></div>
  <div class="bar bar--green"><span>IF YOU CALL TODAY</span></div>

  <div class="address">
    <svg viewBox="0 0 12 16"><path d="M6 0C2.7 0 0 2.6 0 5.9 0 10.3 6 16 6 16s6-5.7 6-10.1C12 2.6 9.3 0 6 0zm0 8.2a2.3 2.3 0 110-4.6 2.3 2.3 0 010 4.6z" fill="#6cc04a"/></svg>
    <p>218 W Harlow Ave.<br>Unit C Tustin,<br>CA 92780</p>
  </div>
  <span class="rule"></span>
  <div class="phone-pill">
    <svg class="phone-pill__icon" viewBox="0 0 24 24"><circle cx="12" cy="12" r="12" fill="#6cc04a"/><path d="M8.6 6.2l1.6 2.6c.3.5.2 1-.2 1.4l-.9.8c.7 1.6 2 2.9 3.6 3.6l.8-.9c.4-.4.9-.5 1.4-.2l2.6 1.6c.5.3.6.9.3 1.4l-.8 1.1c-.5.7-1.4 1-2.2.8-3.9-1-6.9-4-7.9-7.9-.2-.8.1-1.7.8-2.2l1.1-.8c.5-.3 1.1-.2 1.4.3z" fill="#fff"/></svg>
    714-555-0148
  </div>
  <p class="abs web">www.go<span class="accent">brimvale</span>.com</p>

  <div class="brand"><span class="brand__dot"></span><span class="brand__name">BRIMVALE</span></div>
  <p class="license">LICENSE # PR 4102</p>
  <div class="stamp-box" aria-label="Postage stamp area"></div>
  <span class="address-line" style="top:362px"></span>
  <span class="address-line" style="top:427px"></span>
  <span class="address-line" style="top:493px"></span>
</section>

</body>
</html>
```